Business Card Design for a Personal Trainer

I need a business card design for my job as a personal trainer. It should have a unique, modern and exclusive design. On the front there should be only my logo with my name and my job. 0162/3819204 Tobias Lendhart Wiesengrundweg 14 80417 Munich Germany The most important contact information is the web adress. it can be bigger than the rest, but its not necessary. The card should be 8,5cmx5,5cm big. Font: Roboto. Colors: black, white, gray, 56c1ff.

```html
<!DOCTYPE html>
<html lang="de">
<head>
<meta charset="utf-8">
<title>Tobias Lendhart – Personal Trainer Visitenkarte</title>
<link href="https://fonts.googleapis.com/css2?family=Roboto:wght@300;400;500&display=swap" rel="stylesheet">
<style>
  :root {
    --stage: #3c434b;
    --card-black: #141414;
    --card-navy-dark: #0a1119;
    --card-navy: #1a2e42;
    --accent: #56c1ff;
    --white: #ffffff;
    --gray: #b9bec4;
    --photo-light: #6f7armed;
  }
  * { margin: 0; padding: 0; box-sizing: border-box; }
  html, body {
    width: 1200px;
    height: 960px;
    overflow: hidden;
    background: var(--stage);
    font-family: "Roboto", sans-serif;
  }
  .sheet {
    width: 1200px;
    height: 960px;
    display: flex;
    align-items: center;
    justify-content: center;
    gap: 40px;
  }
  .card {
    position: relative;
    width: 540px;
    height: 350px;
    overflow: hidden;
    box-shadow: 0 14px 30px rgba(0, 0, 0, 0.35);
  }

  /* Front */
  .card--front {
    background: var(--card-black);
    display: flex;
    flex-direction: column;
    align-items: center;
    justify-content: center;
  }
  .brand {
    display: flex;
    align-items: center;
    gap: 14px;
  }
  .brand__square {
    width: 22px;
    height: 22px;
    background: var(--white);
  }
  .brand__name {
    color: var(--white);
    font-weight: 400;
    font-size: 34px;
    letter-spacing: 2px;
    text-transform: uppercase;
  }
  .job-line {
    display: flex;
    align-items: center;
    gap: 12px;
    margin-top: 8px;
  }
  .job-line__rule {
    width: 62px;
    height: 1px;
    background: var(--white);
  }
  .job-line__text {
    color: var(--white);
    font-weight: 300;
    font-size: 13px;
    letter-spacing: 5px;
    text-transform: uppercase;
  }

  /* Back */
  .card--back {
    background:
      radial-gradient(ellipse at 35% 45%, var(--card-navy) 0%, var(--card-navy-dark) 75%);
  }
  .contact {
    position: absolute;
    right: 252px;
    top: 78px;
    text-align: right;
    color: var(--gray);
    font-weight: 400;
    font-size: 15px;
    line-height: 1.3;
  }
  .contact__name {
    color: var(--accent);
    font-size: 27px;
    line-height: 1.05;
  }
  .contact__role {
    font-size: 10px;
    font-weight: 300;
    margin-bottom: 6px;
  }
  .contact__phone {
    color: var(--accent);
    font-size: 29px;
    line-height: 1.1;
    margin-bottom: 2px;
  }
  .contact__address { margin-bottom: 12px; }
  .divider {
    position: absolute;
    left: 302px;
    top: 70px;
    width: 3px;
    height: 210px;
    background: var(--accent);
  }
  .portrait {
    position: absolute;
    left: 330px;
    top: 36px;
    width: 195px;
    height: 314px;
    background: radial-gradient(ellipse at 50% 40%, #6e7378 0%, #3a3e43 55%, rgba(20, 30, 42, 0) 90%);
  }
</style>
</head>
<body>
  <main class="sheet">
    <section class="card card--front" aria-label="Vorderseite">
      <div class="brand">
        <span class="brand__square"></span>
        <span class="brand__name">Tobias Lendhart</span>
      </div>
      <div class="job-line">
        <span class="job-line__rule"></span>
        <span class="job-line__text">Personal Trainer</span>
        <span class="job-line__rule"></span>
      </div>
    </section>

    <section class="card card--back" aria-label="Rückseite">
      <div class="contact">
        <p class="contact__name">Tobias Lendhart</p>
        <p class="contact__role">Personal Trainer</p>
        <p class="contact__phone">0162 3819 - 204</p>
        <p class="contact__address">Wiesengrundweg 14<br>80417 München</p>
        <p class="contact__email">t.lendhart@postfeld.de</p>
        <p class="contact__web">www.tobiaslendhart.de</p>
      </div>
      <span class="divider"></span>
      <div class="portrait" role="img" aria-label="Schwarz-weiß Porträt des Trainers mit verschränkten Armen"></div>
    </section>
  </main>
</body>
</html>
```